Interior Design/ decoration business card design

This card is for my Interior Design and Decoration business and later I will also be selling homewares. I would like the card to be very simple in design and like either white, duck egg blue , aquas or metallics on a flat mat card excellent quality card. It needs to be well designed as that is my field. I dont like fuss, the simpler the better. I would like a styalised brim under the name brim if possible. SIMPLE, STYLISH, CLASSIC, TASTEFUL

Target Market(s)

40 + year olds who are building or rennovating.

Industry/Entity Type

Business

Contact Information for Business Card

Brim
styling, design, homeware

Marnie Callow
p 0427163958
e marnie@brimhouse.com.au
w brimhouse.com.au

Requirements
Must have
• very simple, stylish, classic, sophisticated. Simple and easy to read text that is a print similar to attached image. I like simple round A's though not as in attached image.

Double sided. It wont save as double sided for some reason!!
Should not have
• not too much colour, No animated / cartoon pictures.

```html
<!DOCTYPE html>
<html lang="en">
<head>
<meta charset="utf-8">
<title>Brim business card</title>
<link rel="stylesheet" href="https://fonts.googleapis.com/css2?family=Oswald:wght@500&family=Exo+2:wght@300;500&display=swap">
<style>
  :root {
    --page-bg: #d6d6d6;
    --card-bg: #ffffff;
    --ink: #3a2f2a;
    --map-tone: #f1f1f1;
    --shadow: rgba(0, 0, 0, 0.18);
  }
  * { box-sizing: border-box; margin: 0; padding: 0; }
  html, body {
    width: 1200px;
    height: 1002px;
    overflow: hidden;
    background: var(--page-bg);
  }
  .sheet {
    width: 1200px;
    height: 1002px;
    display: flex;
    flex-direction: column;
    align-items: center;
    justify-content: center;
    gap: 40px;
  }
  .card {
    position: relative;
    width: 780px;
    height: 446px;
    background: var(--card-bg);
    box-shadow: 0 8px 24px var(--shadow);
    overflow: hidden;
    color: var(--ink);
  }
  .card__map {
    position: absolute;
    inset: 0;
    background: radial-gradient(ellipse at 45% 50%, var(--map-tone) 0%, var(--card-bg) 75%);
  }
  .wordmark {
    position: absolute;
    display: flex;
    align-items: center;
    gap: 14px;
    font-family: "Exo 2", sans-serif;
    font-weight: 300;
    color: var(--ink);
    letter-spacing: 1px;
  }
  .wordmark__dot {
    width: 12px;
    height: 12px;
    border-radius: 50%;
    background: var(--ink);
  }
  .card--back .wordmark {
    left: 50%;
    top: 50%;
    transform: translate(-50%, -50%);
    font-size: 84px;
  }
  .card--front .wordmark {
    left: 579px;
    top: 222px;
    transform: translate(-50%, -50%);
    font-size: 56px;
  }
  .identity {
    position: absolute;
    left: 52px;
    top: 86px;
    width: 310px;
  }
  .identity__name {
    font-family: "Oswald", sans-serif;
    font-weight: 500;
    font-size: 44px;
    line-height: 1;
    text-transform: uppercase;
    letter-spacing: 0.5px;
    white-space: nowrap;
  }
  .identity__role {
    margin-top: 6px;
    font-family: "Exo 2", sans-serif;
    font-weight: 500;
    font-size: 17px;
    letter-spacing: 2.5px;
    text-transform: uppercase;
  }
  .rule {
    position: absolute;
    background: var(--ink);
  }
  .rule--horizontal { left: 0; top: 176px; width: 380px; height: 3px; }
  .rule--vertical { left: 378px; top: 112px; width: 3px; height: 228px; }
  .contacts {
    position: absolute;
    left: 40px;
    top: 198px;
    width: 330px;
    font-family: "Exo 2", sans-serif;
    font-weight: 500;
    font-size: 14px;
    letter-spacing: 0.3px;
  }
  .contacts__row {
    display: flex;
    gap: 20px;
    margin-bottom: 16px;
  }
  .contact {
    display: flex;
    align-items: center;
    gap: 8px;
    white-space: nowrap;
  }
  .contact--short { width: 118px; }
  .contact svg { width: 15px; height: 15px; flex: none; fill: var(--ink); }
</style>
</head>
<body>
<main class="sheet">

  <section class="card card--back" aria-label="Card back">
    <div class="card__map" role="img" aria-label="Faint world map background"></div>
    <div class="wordmark"><span class="wordmark__dot"></span>brim</div>
  </section>

  <section class="card card--front" aria-label="Card front">
    <div class="card__map" role="img" aria-label="Faint world map background"></div>

    <header class="identity">
      <h1 class="identity__name">Marnie Callow</h1>
      <p class="identity__role">General Manager</p>
    </header>

    <div class="rule rule--horizontal"></div>
    <div class="rule rule--vertical"></div>

    <div class="contacts">
      <div class="contacts__row">
        <span class="contact contact--short">
          <svg viewBox="0 0 16 16" aria-hidden="true"><path d="M3.5 1.5l2.5 0 1 3.5-1.6 1.2c.8 1.8 2.2 3.2 4 4l1.2-1.6 3.5 1v2.5c0 .8-.7 1.4-1.5 1.4C6.8 13.5 2.5 9.2 2.1 3c0-.8.6-1.5 1.4-1.5z"/></svg>
          0427 163 958
        </span>
        <span class="contact">
          <svg viewBox="0 0 16 16" aria-hidden="true"><path d="M1 3h14v10H1z M2 4l6 5 6-5" fill="none" stroke="#3a2f2a" stroke-width="1.5"/></svg>
          marnie@brimhouse.com.au
        </span>
      </div>
      <div class="contacts__row">
        <span class="contact contact--short">
          <svg viewBox="0 0 16 16" aria-hidden="true"><path d="M4 1h8v14H4z" fill="none" stroke="#3a2f2a" stroke-width="1.6"/><circle cx="8" cy="12.5" r="1"/></svg>
          0427 163 958
        </span>
        <span class="contact">
          <svg viewBox="0 0 16 16" aria-hidden="true"><g fill="none" stroke="#3a2f2a" stroke-width="1.3"><circle cx="8" cy="8" r="6.5"/><ellipse cx="8" cy="8" rx="3" ry="6.5"/><path d="M1.5 8h13M2.5 4.5h11M2.5 11.5h11"/></g></svg>
          brimhouse.com.au
        </span>
      </div>
      <div class="contacts__row">
        <span class="contact">
          <svg viewBox="0 0 16 16" aria-hidden="true"><path d="M8 0.5C5 0.5 3 2.7 3 5.4 3 9 8 15.5 8 15.5S13 9 13 5.4C13 2.7 11 0.5 8 0.5zm0 7a2 2 0 110-4 2 2 0 010 4z"/></svg>
          14 Alder Lane, Level 3, Fern Street
        </span>
      </div>
    </div>

    <div class="wordmark"><span class="wordmark__dot"></span>brim</div>
  </section>

</main>
</body>
</html>
```